Real Estate Card Design

I need a new business card! Below you will find my headshot, the company logo and a copy of my previous business card.

The card must contain the following information:

Dana Wexley
Sales Representative
FERNBROOK HOMES REALTY INC BROKERGE
204-517 Marsh Rd E, Oshawa ON L1H 4K7
Cell: 905-618-3074 Office:905-481-2696
www.danawexley.example dana@homesbywexley.example

I would like the card to portray security and class all the while being fresh and contemporary. I hold the key....

```html
<!DOCTYPE html>
<html lang="en">
<head>
<meta charset="utf-8">
<title>Dana Wexley — Business Card</title>
<link rel="stylesheet" href="https://fonts.googleapis.com/css2?family=Noto+Serif:wght@400&family=Roboto:wght@400&display=swap">
<style>
  :root {
    --page-bg: #e9e6e2;
    --card-sky: #80d3f5;
    --brand-blue: #1ea3e3;
    --ink: #15171f;
    --white: #ffffff;
    --suit-navy: #141b2b;
    --portrait-light: #c9b9a4;
  }
  * { margin: 0; padding: 0; box-sizing: border-box; }
  html, body {
    width: 1200px; height: 989px; overflow: hidden;
    background: var(--page-bg);
  }
  .business-card {
    position: absolute;
    left: 50px; top: 178px;
    width: 1100px; height: 632px;
    background: var(--card-sky);
    overflow: hidden;
  }
  .brand {
    position: absolute;
    left: 70px; top: 58px;
    width: 330px;
    text-align: center;
  }
  .brand-square {
    display: block;
    width: 136px; height: 96px;
    margin: 0 auto 14px;
    background: var(--brand-blue);
  }
  .brand-name {
    font-family: "Noto Serif", serif;
    font-weight: 400;
    font-size: 24px;
    line-height: 1.2;
    letter-spacing: 0.5px;
    color: var(--ink);
  }
  .agent {
    position: absolute;
    left: 62px; top: 258px;
    font-family: "Noto Serif", serif;
    color: var(--ink);
  }
  .agent-name { font-size: 38px; font-weight: 400; line-height: 1.15; }
  .agent-title { font-size: 25px; font-weight: 400; line-height: 1.3; }
  .office-address {
    position: absolute;
    left: 64px; top: 356px;
    font-family: "Roboto", sans-serif;
    font-size: 25px;
    line-height: 33px;
    color: var(--white);
    font-style: normal;
  }
  .contact-list {
    position: absolute;
    left: 64px; top: 440px;
    list-style: none;
    font-family: "Roboto", sans-serif;
    font-size: 26px;
    color: var(--white);
  }
  .contact-item {
    display: flex; align-items: center;
    height: 35.5px;
  }
  .contact-icon {
    width: 26px; height: 26px;
    margin-right: 16px;
    flex: none;
  }
  .portrait {
    position: absolute;
    right: 0; bottom: 0;
    width: 480px; height: 605px;
    border-radius: 200px 0 0 0;
    background: linear-gradient(180deg, var(--portrait-light) 0%, #8c7a6a 30%, var(--suit-navy) 55%, #0c111c 100%);
  }
</style>
</head>
<body>
  <section class="business-card">
    <div class="brand">
      <span class="brand-square"></span>
      <p class="brand-name">FERNBROOK HOMES<br>REALTY INC BROKERGE</p>
    </div>

    <div class="agent">
      <h1 class="agent-name">Dana Wexley</h1>
      <p class="agent-title">Sales Representative</p>
    </div>

    <address class="office-address">204-517 Marsh Rd E,<br>Oshawa ON L1H 4K7</address>

    <ul class="contact-list">
      <li class="contact-item">
        <svg class="contact-icon" viewBox="0 0 24 24"><path fill="#15171f" d="M6.6 10.8c1.4 2.8 3.8 5.1 6.6 6.6l2.2-2.2c.3-.3.7-.4 1-.2 1.1.4 2.3.6 3.6.6.6 0 1 .4 1 1V20c0 .6-.4 1-1 1C10.6 21 3 13.4 3 4c0-.6.4-1 1-1h3.5c.6 0 1 .4 1 1 0 1.3.2 2.5.6 3.6.1.3 0 .7-.2 1z"/></svg>
        <span>905-481-2696</span>
      </li>
      <li class="contact-item">
        <svg class="contact-icon" viewBox="0 0 24 24"><rect x="6" y="2" width="12" height="20" rx="2" fill="#15171f"/><rect x="8" y="5" width="8" height="12" fill="#80d3f5"/></svg>
        <span>905-618-3074</span>
      </li>
      <li class="contact-item">
        <svg class="contact-icon" viewBox="0 0 24 24"><rect x="2" y="6" width="20" height="13" fill="#15171f"/><path d="M2 6l10 7 10-7" fill="none" stroke="#80d3f5" stroke-width="1.6"/></svg>
        <span>dana@homesbywexley.example</span>
      </li>
      <li class="contact-item">
        <svg class="contact-icon" viewBox="0 0 24 24"><circle cx="12" cy="12" r="10" fill="#15171f"/><ellipse cx="12" cy="12" rx="4" ry="10" fill="none" stroke="#80d3f5" stroke-width="1.4"/><path d="M2 12h20" stroke="#80d3f5" stroke-width="1.4"/></svg>
        <span>www.danawexley.example</span>
      </li>
    </ul>

    <div class="portrait" role="img" aria-label="Portrait of Dana Wexley in a navy pinstripe suit, holding up a house key"></div>
  </section>
</body>
</html>
```